Business Card design project for new family-run construction business

We need a logo and business card designed for a new construction company. We want to convey a professional, but approachable image. We hope to be servicing small residential clients as well as large commercial contracts as well.
Our business will employ a single "Hydro excavator" truck, which can be used for multiple purposes: vacuuming up dirt or water, digging holes, clearing sewer blockages and so on.
We are open to different colour schemes, however blue and white, or yellow/green would be good combinations. We are open to multiple colours (2-4), so long as they are complimentary.

EDIT: Let's not put much emphasis on the octopus... unless it's very clear that the arms are actual vacuum hoses, it won't make sense. An octopus on it's own has little to do with our business.

Please also do not use actual photos of hydro-vac trucks. This is not the aesthetic we are going for.

**The logo should instead be: A stylized outline of a hydrovac truck (a line drawing or digital version of a line-drawing). See the two examples in the attached images of hydrovac trucks. I've also included a very crude pen outline as a reference. Please use your artistic discretion and talent (as I clearly have none) to make something that looks much nicer. Thanks for your efforts!**

The front of the card should have the following elements:
Logo
Name: R & T Hydro Excavation and Flushign
Two phone numbers: Direct and Office
Email address
Website
It should also have the name of the employee and their job title
At the bottom of the card it should say (in a noticeable way): "24/7 Emergency Calls Welcome"

The back of the card should have the following elements:
"20 Years Experience"
"A Canadian Family Run Business"
A small maple-leaf logo that is in a similar style to the rest of the card/logos in the bottom right corner of the back of the card. (see attached)

**We have just added a number of business card designs that really appeal to us to offer inspiration.**

Reason: We have not received designs that hit the mark of what we are looking for. Feedback has been posted, so we would like to provide the designers more time.

Target Market(s)

Commercial and residential customers. As big as large malls and office buildings, as small single-family home owners

Industry/Entity Type

Construction Company

Contact Information for Business Card

We have just added a number of business card designs that really appeal to us to offer inspiration.

Logo
Email address
Website

"20 Years Experience"

Logo Text

R & T Hydro Excavation and Flushing

Font styles to use
Serif
Sans Serif
Other font styles liked:
• Helvetica, Futura, Impact, bold strong, modern fonts that convey a sense of design and style

Colors
0592cd
ec1f27
9bcb3c

Requirements
Must have
• The front of the card should have the following elements:
• Logo
• Name: R & T Hydro Excavation and Flushign
• Two phone numbers: Direct and Office
• Email address
• Website
• It should also have the name of the employee and their job title
• At the bottom of the card it should say (in a noticeable way): "24/7 Emergency Calls Welcome"
• The back of the card should have the following elements:
• "20 Years Experience"
• "A Canadian Family Run Business"
• A small maple-leaf logo that is in a similar style to the rest of the card/logos in the bottom right corner of the back of the card. (see attached)
Nice to have
• The card does not have to be a perfect rectangle. We are open to rounded corners or cut out elements.
• Also embossing, engraving, adding highlighted/glossy layers (spot glass?), or any other effect that will give the card a unique look/feel is more than welcome.
• We would love to have a card that stands out from others and is compelling to look at it, so we are happy to incorporate any sort of modern printing technology to bring out the design.
• Please feel encouraged to be creative and design something unique, especially for this industry.
• Our dream would be if a Scandinavian architect were to go into the construction business and design this business card ;)
Should not have
• Photographs

```html
<!DOCTYPE html>
<html lang="en">
<head>
<meta charset="utf-8">
<title>R &amp; T Hydro Excavation &amp; Flushign – Business Card</title>
<link rel="stylesheet" href="https://fonts.googleapis.com/css2?family=Carlito:wght@400;700&display=swap">
<style>
  :root {
    --card-blue: #0a10e6;
    --ink-blue: #1414d2;
    --white: #ffffff;
    --charcoal: #333333;
    --leaf-red: #e3161d;
    --truck-grey-light: #f1f1f1;
    --truck-grey: #dedede;
  }
  html, body {
    margin: 0;
    padding: 0;
    width: 1200px;
    height: 850px;
    overflow: hidden;
    background: var(--white);
  }
  .canvas {
    position: relative;
    width: 1200px;
    height: 850px;
  }
  .business-card {
    position: absolute;
    left: 173px;
    top: 133px;
    width: 856px;
    height: 464px;
    display: block;
  }
  .card-type {
    font-family: "Carlito", "Calibri", sans-serif;
    font-weight: 700;
  }
  .company-name { fill: var(--white); font-size: 41px; }
  .pin-contact { fill: var(--charcoal); font-size: 40px; font-weight: 400; }
  .pin-details { fill: var(--leaf-red); font-size: 33px; stroke: #5a1010; stroke-width: 0.8px; paint-order: stroke; }
  .contact-line { fill: var(--ink-blue); font-size: 27px; }
</style>
</head>
<body>
<main class="canvas">
  <svg class="business-card" viewBox="0 0 1070 580" xmlns="http://www.w3.org/2000/svg">
    <defs>
      <radialGradient id="pinRing" cx="50%" cy="40%" r="60%">
        <stop offset="0%" stop-color="#8fa6ee"/>
        <stop offset="100%" stop-color="#1a35cf"/>
      </radialGradient>
      <linearGradient id="pinBeam" x1="0" y1="0" x2="0" y2="1">
        <stop offset="0%" stop-color="#eef2ff"/>
        <stop offset="100%" stop-color="#3f5de0"/>
      </linearGradient>
      <linearGradient id="truckTone" x1="0" y1="0" x2="0" y2="1">
        <stop offset="0%" stop-color="var(--truck-grey-light)"/>
        <stop offset="100%" stop-color="var(--truck-grey)"/>
      </linearGradient>
    </defs>

    <rect class="card-frame" x="0" y="0" width="1070" height="580" fill="var(--card-blue)"/>
    <path class="card-face"
          d="M20,114 C140,72 280,58 390,58 C600,60 800,120 1050,219 L1050,561 L20,561 Z"
          fill="var(--white)"/>

    <text class="card-type company-name" x="1046" y="51" text-anchor="end">R &amp; T Hydro Excavation &amp; Flushign</text>

    <rect class="truck-mark" x="89" y="287" width="468" height="244" rx="22"
          fill="url(#truckTone)" role="img"
          aria-label="Grey line-drawing of a hydrovac truck with tank, hose reels and cab"/>

    <g class="contact-pin">
      <path d="M904,364 L812,240 A105,105 0 1 1 996,240 Z" fill="url(#pinRing)"/>
      <path d="M904,364 L850,268 L958,268 Z" fill="url(#pinBeam)"/>
      <circle cx="904" cy="190" r="88" fill="var(--white)"/>
      <rect class="leaf-mark" x="878" y="114" width="54" height="54" fill="var(--leaf-red)"
            role="img" aria-label="Red maple leaf"/>
      <text class="card-type pin-contact" x="904" y="210" text-anchor="middle">CONTACT</text>
      <text class="card-type pin-details" x="907" y="243" text-anchor="middle">DETAILS</text>
    </g>

    <text class="card-type contact-line" x="1039" y="389" text-anchor="end">2 phone numbers: Direct &amp; Office</text>
    <text class="card-type contact-line" x="894" y="420" text-anchor="middle">Email address</text>
    <text class="card-type contact-line" x="894" y="452" text-anchor="middle">Website</text>
    <text class="card-type contact-line" x="1035" y="483" text-anchor="end">Employee and their job title</text>
    <text class="card-type contact-line" x="1040" y="517" text-anchor="end">24/7 Emergency Calls Welcome</text>
  </svg>
</main>
</body>
</html>
```